Realty Group Needs Classy, Contemporary Letterhead Design

We need a letterhead design for a new realty company located in NY, USA. We buy investment properties to rehabilitate and or keep in our rental portfolio.

```html
<!DOCTYPE html>
<html lang="en">
<head>
<meta charset="utf-8">
<title>Halvorsen Realty Group – Letterhead</title>
<link href="https://fonts.googleapis.com/css2?family=Poppins:wght@400;600;700&family=Questrial&display=swap" rel="stylesheet">
<style>
  :root {
    --brand-purple: #4b2a86;
    --ink: #2b2b2b;
    --body-ink: #333333;
    --paper: #ececec;
    --paper-light: #f3f3f3;
    --rule: #5a5a5a;
  }
  html, body { margin: 0; padding: 0; overflow: hidden; }
  body { width: 960px; height: 1200px; background: var(--paper); }
  .letterhead {
    position: relative;
    width: 960px; height: 1200px;
    background: linear-gradient(100deg, var(--paper-light) 0%, var(--paper) 60%, #e6e6e6 100%);
    overflow: hidden;
    font-family: "Questrial", "Century Gothic", sans-serif;
    color: var(--ink);
  }
  .brand {
    position: absolute; left: 89px; top: 96px;
    display: flex; align-items: center; gap: 12px;
  }
  .brand-mark {
    width: 22px; height: 22px; background: var(--brand-purple);
  }
  .brand-name {
    font-family: "Poppins", sans-serif; font-weight: 600;
    font-size: 26px; line-height: 1; color: var(--brand-purple);
    white-space: nowrap;
  }
  .divider-thin {
    position: absolute; left: 322px; top: 229px; width: 1px; height: 470px;
    background: var(--rule);
  }
  .divider-bar {
    position: absolute; left: 318px; top: 699px; width: 9px; height: 244px;
    background: var(--brand-purple);
  }
  .contact {
    position: absolute; right: 665px; top: 727px;
    text-align: right; font-style: normal;
    font-family: "Poppins", sans-serif;
    font-size: 14.5px; line-height: 16.5px; color: #1e1e1e;
  }
  .contact-company { color: var(--brand-purple); font-weight: 600; }
  .contact-numbers { margin-top: 18px; line-height: 18px; }
  .contact-label { color: var(--brand-purple); font-weight: 600; margin-right: 4px; }
  .contact-web { margin-top: 14px; color: var(--brand-purple); font-weight: 700; }
  .letter {
    position: absolute; left: 377px; top: 223px; width: 503px;
  }
  .salutation { font-size: 23px; line-height: 30px; margin: 0 0 40px; }
  .letter p.body {
    font-size: 13.6px; line-height: 18.3px; margin: 0 0 18px;
    letter-spacing: 0.15px;
    text-align: justify; hyphens: auto; color: var(--body-ink);
  }
  .closing { font-size: 13.6px; margin: 36px 0 0; color: var(--body-ink); }
  .signature {
    position: absolute; left: 376px; top: 880px; width: 125px; height: 70px;
    background: linear-gradient(120deg, rgba(40,40,40,0.12), rgba(40,40,40,0.04));
    border-radius: 4px;
  }
</style>
</head>
<body>
<main class="letterhead">
  <header class="brand">
    <span class="brand-mark"></span>
    <span class="brand-name">Halvorsen Realty Group, LLC</span>
  </header>

  <div class="divider-thin"></div>
  <div class="divider-bar"></div>

  <address class="contact">
    <div class="contact-company">Halvorsen LLC</div>
    <div>4120 Linden Court<br>Albany New York<br>NY 12203</div>
    <div class="contact-numbers">
      <div><span class="contact-label">T</span>: 518-204-7731</div>
      <div><span class="contact-label">C</span>: 518-390-6142</div>
      <div><span class="contact-label">F</span>: 518-447-2095</div>
      <div><span class="contact-label">E</span>: info@halvorsenrealty.com</div>
    </div>
    <div class="contact-web">halvorsenrealty.com</div>
  </address>

  <section class="letter">
    <p class="salutation">Dear Mr. Carter,</p>
    <p class="body">Lorem ipsum dolor sit amet, consectetur adipiscing elit. Donec orci purus, luctus vitae dignissim eu, iaculis sed purus. Vivamus faucibus, ipsum nec aliquet viverra, leo mauris condimentum ligula, sit amet sagittis enim ligula quis arcu. Nam egestas tortor id nisi porttitor mattis. In tortor ante, ultricies in suscipit a, tempus non massa. Vivamus et auctor mi. Fusce vel massa nulla. Phasellus nec eros mauris, et scelerisque orci.</p>
    <p class="body">Donec malesuada orci vitae nulla accumsan porta a id massa. Quisque accumsan iaculis magna sit amet fringilla. Maecenas consequat, magna eget tincidunt semper, odio nibh rutrum mi, id feugiat ante nisi eu risus. Vestibulum nunc orci, rhoncus a placerat in, ultricies in mi. Cras mattis varius eros, vel fringilla nisi suscipit eget. Quisque scelerisque sagittis nulla at porttitor.</p>
    <p class="body">Sed id augue vitae urna euismod commodo aliquet a quam. Pellentesque arcu velit, cursus et malesuada ut, consequat et diam. Nullam erat sem, rhoncus id ullamcorper vitae, rhoncus et arcu. In ultricies ultricies nulla, ut rutrum nisi iaculis at. Donec eu magna a metus ornare faucibus. Fusce aliquet faucibus ultricies. Morbi semper, est id tincidunt gravida, sem arcu adipiscing lacus, ac bibendum nulla leo eu purus. Quisque nec diam sed risus consectetur a ccumsan quis quis nibh. Vestibulum id purus lorem.</p>
    <p class="body">It is a long established fact that a reader will be distracted by the readable content of a page when looking at its layout. The point of using Lorem Ipsum is that it has a more-or-less normal distribution of letters, as opposed to using 'Content here, content here', making it look like readable English. Many desktop publishing packages</p>
    <p class="closing">Sincerely,</p>
  </section>

  <div class="signature" role="img" aria-label="Handwritten signature of the sender"></div>
</main>
</body>
</html>
```